Automotive eCommerce Business looking for a business card design

Looking for a clean and simple business card design. Our company name is "Brindle Auto" and we are a company specializing in the ecommerce sales of automotive parts, specifically for pick up trucks and large SUVs. Our company colours are red, black, and white.

Feel free to use the logo provided or create a new logo that you seem fit. Looking forward to your creative ideas!

Industry/Entity Type

Automotive

Contact Information for Business Card

We were thinking of a possibly two-sided design featuring just the logo and company name on one side, and personal information on the other side. Single sided designs will be considered as well.

Font styles to use
Serif
Sans Serif
Decorative

Colors
ec1f27
ffffff
000000

Requirements
Must have
• Space for employee's name, title, phone number and email address, along with the company address and website somewhere.

```html
<!DOCTYPE html>
<html lang="en">
<head>
<meta charset="utf-8">
<title>Brindle Auto Ltd – Business Card</title>
<link rel="stylesheet" href="https://fonts.googleapis.com/css2?family=Open+Sans:wght@400;600;700&display=swap">
<style>
  :root {
    --brand-red: #b01e24;
    --brand-black: #111111;
    --card-white: #ffffff;
    --card-dark: #222222;
    --text-dark: #1a1a1a;
    --page-bg: #e9e6e2;
  }
  * { box-sizing: border-box; margin: 0; padding: 0; }
  html, body {
    width: 1200px; height: 900px; overflow: hidden;
    background: var(--page-bg);
    font-family: "Open Sans", sans-serif;
  }
  .stage {
    position: relative; width: 1200px; height: 900px;
  }
  .card {
    position: absolute; left: 300px;
    width: 600px; height: 343px;
    overflow: hidden;
    box-shadow: 0 6px 18px rgba(0,0,0,0.18);
  }
  /* Back side */
  .card--back {
    top: 90px;
    background: var(--card-dark);
    display: flex; flex-direction: column; align-items: center; justify-content: center;
    gap: 14px;
  }
  .card--back .brand-mark { background: var(--card-white); }
  .card--back .brand-name { color: var(--card-white); }

  .brand-mark {
    width: 70px; height: 70px; border-radius: 6px;
  }
  .brand-name {
    font-weight: 700; font-size: 31px; letter-spacing: 0.5px; line-height: 1;
  }

  /* Front side */
  .card--front {
    top: 467px;
    background: var(--card-white);
  }
  .card-graphics { position: absolute; inset: 0; }
  .holder {
    position: absolute; left: 74px; top: 18px;
  }
  .holder-name {
    color: var(--brand-red); font-weight: 700; font-size: 21px; line-height: 1.1;
  }
  .holder-title {
    color: var(--text-dark); font-size: 11px; margin-top: 1px;
  }
  .contact {
    position: absolute; left: 34px; top: 126px;
    color: var(--text-dark); font-size: 13.5px; line-height: 19px;
    list-style: none;
  }
  .contact-address { margin-bottom: 4px; }
  .contact-row { display: flex; align-items: center; gap: 7px; }
  .contact-row svg { width: 10px; height: 10px; fill: var(--brand-red); flex: none; }
  .front-brand {
    position: absolute; left: 350px; top: 95px;
    display: flex; flex-direction: column; align-items: center; gap: 12px;
    transform: translateX(-50%);
  }
  .front-brand .brand-mark { background: var(--brand-red); width: 78px; height: 78px; }
  .front-brand .brand-name { color: var(--brand-black); white-space: nowrap; }
</style>
</head>
<body>
<main class="stage">

  <section class="card card--back" aria-label="Card back">
    <span class="brand-mark" aria-hidden="true"></span>
    <span class="brand-name">Brindle Auto Ltd</span>
  </section>

  <section class="card card--front" aria-label="Card front">
    <svg class="card-graphics" viewBox="0 0 600 343" width="600" height="343" aria-hidden="true">
      <polygon points="0,0 52,0 40,30 0,30" fill="var(--brand-red)"/>
      <polygon points="46,30 60,0 70,0 70,30" fill="var(--brand-black)"/>
      <polygon points="0,250 300,250 286,274 0,274" fill="var(--brand-red)"/>
      <polygon points="296,274 312,250 600,250 600,250" fill="var(--brand-red)" opacity="0"/>
      <polygon points="300,276 316,254 600,254 600,300 300,300" fill="var(--brand-black)" transform="translate(0,10)"/>
    </svg>

    <div class="holder">
      <p class="holder-name">Marcus Hale</p>
      <p class="holder-title">Managing Director</p>
    </div>

    <ul class="contact">
      <li class="contact-address">48 Foundry Road, Unit 7<br>Westhaven, 204518.</li>
      <li class="contact-row">
        <svg viewBox="0 0 10 10"><path d="M2 0.5 L3.6 2.6 L2.8 3.6 C3.4 5 4.8 6.4 6.3 7.1 L7.3 6.3 L9.5 7.9 L8.5 9.6 C4.5 9.4 0.6 5.6 0.4 1.4 Z"/></svg>
        044-210 987 654
      </li>
      <li class="contact-row">
        <svg viewBox="0 0 10 10"><path d="M0 2 H10 V8.5 H0 Z M0.6 2.4 L5 5.6 L9.4 2.4" stroke="#fff" stroke-width="0.8"/></svg>
        info@brindlemail.com
      </li>
      <li class="contact-row">
        <svg viewBox="0 0 10 10"><path d="M4 6 L6 4 M3.2 4.2 L1.6 5.8 A1.6 1.6 0 0 0 4.2 8.4 L5.8 6.8 M6.8 5.8 L8.4 4.2 A1.6 1.6 0 0 0 5.8 1.6 L4.2 3.2" fill="none" stroke="var(--brand-red)" stroke-width="1.2"/></svg>
        www.brindleparts.com
      </li>
    </ul>

    <div class="front-brand">
      <span class="brand-mark" aria-hidden="true"></span>
      <span class="brand-name">Brindle Auto Ltd</span>
    </div>
  </section>

</main>
</body>
</html>
```